Cover für Gedichtbuch
Zielgruppe
Das Buch soll jungen und alten Menschen gefallen. Zielgruppe sind aber vor allem junge Leser zwischen 18 und Mitte 20.
Aufgabenstellung
Für das Erstlingswerk von zwei Nachwuchsautoren wird ein Wendecover gesucht. Sprich: Auf der einen Seite stehen Gedichte mit hellen Gedichten (Liebe, Freude, Glück) - die andere Hälfte besteht aus dunklen Gedichten (Tod, Depression). Das Buch soll gedreht werden. Daher sollen die beiden Coverseiten einen Kontrast darstellen.

```html
<!DOCTYPE html>
<html lang="de">
<head>
<meta charset="utf-8">
<title>dunkle Gedichte – Cover</title>
<link rel="stylesheet" href="https://fonts.googleapis.com/css2?family=Jost:wght@400&family=Parisienne&display=swap">
<style>
  :root {
    --ink: #000000;
    --night: #161616;
    --mist: #5e5e5e;
    --ash: #8a8a8a;
    --blood: #c8141c;
    --paper: #f2f2f2;
  }
  html, body {
    margin: 0;
    padding: 0;
    overflow: hidden;
    background: var(--ink);
  }
  .cover {
    position: relative;
    width: 847px;
    height: 1200px;
    background: var(--ink);
    overflow: hidden;
  }
  .cover__art {
    position: absolute;
    inset: 0;
  }
  .cover__author {
    position: absolute;
    left: 20px;
    top: 284px;
    transform: rotate(-90deg);
    transform-origin: left top;
    margin: 0;
    font-family: "Jost", sans-serif;
    font-weight: 400;
    font-size: 29px;
    letter-spacing: 1px;
    line-height: 1;
    color: var(--blood);
    white-space: nowrap;
  }
  .cover__title {
    position: absolute;
    left: 198px;
    top: 818px;
    margin: 0;
    font-family: "Parisienne", cursive;
    font-weight: 400;
    font-size: 80px;
    line-height: 1;
    color: var(--paper);
    white-space: nowrap;
  }
  .cover__themes {
    position: absolute;
    left: 612px;
    top: 902px;
    margin: 0;
    font-family: "Jost", sans-serif;
    font-size: 18px;
    letter-spacing: 0.3px;
    color: var(--paper);
    white-space: nowrap;
  }
</style>
</head>
<body>
<main class="cover">
  <svg class="cover__art" width="847" height="1200" viewBox="0 0 847 1200">
    <defs>
      <radialGradient id="sky-glow">
        <stop offset="0" stop-color="var(--mist)" stop-opacity="0.9"/>
        <stop offset="0.5" stop-color="var(--night)" stop-opacity="0.7"/>
        <stop offset="1" stop-color="var(--ink)" stop-opacity="0"/>
      </radialGradient>
      <radialGradient id="tree-tone">
        <stop offset="0" stop-color="var(--ash)" stop-opacity="0.55"/>
        <stop offset="1" stop-color="var(--ash)" stop-opacity="0"/>
      </radialGradient>
      <radialGradient id="wing-tone">
        <stop offset="0" stop-color="var(--blood)" stop-opacity="1"/>
        <stop offset="0.6" stop-color="var(--blood)" stop-opacity="0.8"/>
        <stop offset="1" stop-color="var(--blood)" stop-opacity="0"/>
      </radialGradient>
      <radialGradient id="ornament-tone">
        <stop offset="0" stop-color="var(--ash)" stop-opacity="0.4"/>
        <stop offset="1" stop-color="var(--ash)" stop-opacity="0"/>
      </radialGradient>
    </defs>
    <ellipse class="sky" cx="330" cy="330" rx="520" ry="330" fill="url(#sky-glow)"/>
    <ellipse class="illustration illustration--tree" cx="200" cy="300" rx="200" ry="250" fill="url(#tree-tone)"
             role="img" aria-label="Kahler weißer Baum mit verästelten Zweigen vor dunklem Nachthimmel"/>
    <ellipse class="illustration illustration--wing" cx="660" cy="500" rx="200" ry="260" transform="rotate(-18 660 500)" fill="url(#wing-tone)"
             role="img" aria-label="Roter gefiederter Flügel mit eingerollter Spitze"/>
    <g class="illustration illustration--ornament" role="img" aria-label="Graue geschwungene Spiralornamente am unteren Rand und rechts">
      <ellipse cx="170" cy="1000" rx="230" ry="150" fill="url(#ornament-tone)"/>
      <ellipse cx="740" cy="1020" rx="150" ry="320" fill="url(#ornament-tone)"/>
    </g>
  </svg>

  <p class="cover__author">Jonas Wendler</p>
  <h1 class="cover__title">dunkle Gedichte</h1>
  <p class="cover__themes">Trauer · Tod · Depressionen</p>
</main>
</body>
</html>
```